Export company based in South America (Ecuador) we export flowers, chocolate, and bananas

We need a website that gives our potential clients and introduction into our company and the different types of commodities we export around the world. We are based in Quito, Ecuador so the website should portray the feel of Ecuadorian landscapes within a modern looking website.
At the moment we are exporting roses, chocolate, and bananas so the website should have an intro to our company and then three different areas that describe our three main commodity. The three different sections should explain why each of the products from Ecuador are some of the best in the world in their categories and the benefits of importing the commodity through our company.
Industry/Entity Type
Commodity
Number of Pages Required
4 page

```html
<!DOCTYPE html>
<html lang="en">
<head>
<meta charset="utf-8">
<title>Valdora – Export Flowers, Chocolate &amp; Bananas</title>
<link href="https://fonts.googleapis.com/css2?family=Montserrat:wght@500;600;700;800&family=Lato:wght@400;700&display=swap" rel="stylesheet">
<style>
:root{
  --green:#3ea30e;
  --green-dark:#2b7c00;
  --green-light:#52c20f;
  --orange:#f59a00;
  --ink:#333333;
  --muted:#666666;
  --paper:#ffffff;
  --soft:#f7f6f4;
  --grey-bg:#efefef;
  --footer:#2b2b2b;
}
*{box-sizing:border-box;margin:0;padding:0}
html,body{width:1200px;height:3580px;overflow:hidden;background:var(--paper)}
body{position:relative;font-family:"Lato",sans-serif;color:var(--ink)}
.abs{position:absolute}
.btn{position:absolute;display:flex;align-items:center;justify-content:center;background:var(--orange);color:#fff;font-family:"Montserrat",sans-serif;font-weight:700;border-radius:30px}

/* header */
.site-header{position:absolute;left:0;top:0;width:1200px;height:94px;background:#fff}
.brand{position:absolute;left:122px;top:20px;display:flex;align-items:center;gap:8px;font-family:"Montserrat",sans-serif;font-weight:700;font-size:40px;color:var(--green)}
.brand-dot{width:14px;height:14px;border-radius:50%;background:var(--orange)}
.main-nav{position:absolute;left:400px;top:34px;display:flex;font-family:"Montserrat",sans-serif;font-weight:600;font-size:16px;color:#444}
.main-nav span{padding:0 22px;border-left:1px solid #ccc;line-height:22px}
.main-nav span:first-child{border:none;color:var(--green)}

/* hero */
.hero{position:absolute;left:0;top:94px;width:1200px;height:660px;background:linear-gradient(180deg,#5b8fd0 0%,#9bbbd8 18%,#6f9a3c 40%,#4f7f26 65%,#7a7a6a 85%,#5e6b3c 100%)}
.hero-title{position:absolute;left:0;width:1200px;top:284px;text-align:center;font-family:"Montserrat",sans-serif;font-weight:800;font-size:70px;color:#fff;text-shadow:0 2px 6px rgba(0,0,0,.3)}
.hero-sub{position:absolute;left:0;width:1200px;top:366px;text-align:center;font-family:"Montserrat",sans-serif;font-weight:700;font-size:34px;color:#fff;text-shadow:0 2px 6px rgba(0,0,0,.3)}
.hero-arrow{position:absolute;top:325px}
.hero-wave{position:absolute;left:0;top:630px}

/* about */
.section-title{position:absolute;left:0;width:1200px;text-align:center;font-family:"Montserrat",sans-serif;font-weight:700}
.about-title{top:766px;font-size:38px;color:var(--green)}
.about-title em{font-style:normal;color:var(--orange)}
.about-text{position:absolute;left:220px;width:760px;top:834px;text-align:center;font-size:16px;line-height:23px;color:#555}
.mountain-band{position:absolute;left:0;top:1120px;width:1200px;height:316px;background:linear-gradient(180deg,#fff 0%,#e4e4e4 45%,#cfcfcf 75%,#e9e9e9 100%)}
.product{position:absolute;top:963px;width:300px}
.product-photo{height:221px;border-radius:4px}
.product-card{position:absolute;left:22px;top:174px;width:262px;height:183px;background:#fff;box-shadow:0 2px 8px rgba(0,0,0,.12);text-align:center}
.product-card h3{margin-top:26px;font-family:"Montserrat",sans-serif;font-weight:700;font-size:22px;color:var(--green)}
.product-card p{margin:10px 18px 0;font-size:13.5px;line-height:20.5px;color:#666}
.product-card .btn{left:66px;top:160px;width:127px;height:34px;font-size:13px}

/* why */
.why{position:absolute;left:0;top:1435px;width:1200px;height:546px;background:linear-gradient(110deg,var(--green-light) 0%,var(--green) 50%,var(--green-dark) 100%)}
.why-photo{position:absolute;left:133px;top:93px;width:457px;height:311px;background:linear-gradient(135deg,#9aa88a,#a6d23a 40%,#7fb520 60%,#4b5f7e)}
.why h2{position:absolute;left:627px;top:94px;font-family:"Montserrat",sans-serif;font-weight:700;font-size:31px;color:#fff}
.why-rule{position:absolute;left:635px;top:142px;width:54px;height:2px;background:#fff}
.why-text{position:absolute;left:635px;top:163px;width:455px;font-size:14.5px;line-height:24.5px;color:#fff}
.why-text p+p{margin-top:12px}
.why .btn{left:631px;top:343px;width:167px;height:46px;font-size:17px}
.why-edge{position:absolute;left:0;top:1880px}

/* benefits */
.benefits{position:absolute;left:0;top:1981px;width:1200px;height:633px;background:var(--soft)}
.benefits-title{top:2016px;font-size:28px;color:#444;font-weight:600}
.hub{position:absolute;left:491px;top:2082px;width:216px;height:216px;border-radius:50%;background:var(--green-dark);border-bottom:8px solid var(--orange);border-right:3px solid var(--orange);display:flex;align-items:center;justify-content:center;font-family:"Montserrat",sans-serif;font-weight:700;font-size:40px;color:#fff}
.benefit{position:absolute;width:160px;text-align:center}
.benefit .ring{width:92px;height:92px;margin:0 auto;border:5px solid var(--green);border-radius:50%;background:#fff;display:flex;align-items:center;justify-content:center}
.benefit h4{margin-top:14px;font-family:"Lato",sans-serif;font-weight:700;font-size:15.5px;color:#222}
.benefit p{font-size:14px;line-height:17px;color:#555}
.benefit .num{margin-top:10px;font-size:27px;color:#aaa;font-family:"Montserrat",sans-serif;font-weight:500}

/* blogs */
.blogs{position:absolute;left:0;top:2614px;width:1200px;height:581px;background:var(--grey-bg)}
.blogs h2{position:absolute;left:138px;top:78px;font-family:"Montserrat",sans-serif;font-weight:600;font-size:33px;color:#333}
.post{position:absolute;top:143px;width:302px}
.post-photo{height:210px}
.post-card{position:absolute;left:21px;top:172px;width:262px;height:172px;background:#fff;text-align:center}
.post-card .date{margin-top:17px;font-family:"Montserrat",sans-serif;font-weight:600;font-size:13.5px;color:var(--orange)}
.post-card h3{margin-top:6px;font-size:14.5px;line-height:19px;font-weight:700;color:#222}
.post-card p{margin-top:9px;font-size:13px;line-height:18px;color:#777}
.post-card .more{margin-top:9px;font-family:"Montserrat",sans-serif;font-weight:700;font-size:11px;color:var(--green)}

/* footer */
.site-footer{position:absolute;left:0;top:3195px;width:1200px;height:385px;background:linear-gradient(180deg,#323232,#252525 60%,#1f1f1f);color:#ddd}
.foot-col{position:absolute;top:62px}
.foot-col h5{font-family:"Montserrat",sans-serif;font-weight:700;font-size:18px;color:#fff;margin-bottom:14px}
.menu-list{font-size:15px;line-height:23px}
.contact-row{display:flex;gap:10px;margin-bottom:14px;font-size:15px;line-height:18px}
.icon-dot{flex:none;width:36px;height:36px;border-radius:50%;background:var(--green);display:flex;align-items:center;justify-content:center}
.signup{width:224px;height:38px;background:#fff;color:#555;font-size:11px;padding:11px 12px;margin-top:10px}
.subscribe{width:116px;height:32px;margin-top:10px;background:var(--green);color:#fff;font-family:"Montserrat",sans-serif;font-weight:700;font-size:14px;display:flex;align-items:center;justify-content:center}
.social{display:flex;gap:10px;align-items:center;margin-bottom:14px}
.social-ring{width:38px;height:38px;border:2px solid #ddd;border-radius:50%}
.social small{display:block;font-size:11px;color:#bbb}
.social span{font-size:15px}
.copyright{position:absolute;left:0;width:1200px;top:344px;text-align:center;font-size:15px;color:var(--orange)}
.foot-rule{position:absolute;left:0;top:320px;width:1200px;height:1px;background:#444}
</style>
</head>
<body>

<header class="site-header">
  <div class="brand"><span class="brand-dot"></span>Valdora</div>
  <nav class="main-nav"><span>About Us</span><span>What We Export</span><span>Why We Are</span><span>Blogs</span><span>Contact Us</span></nav>
</header>

<section class="hero" role="img" aria-label="Green Andean valley with a rocky river under a blue sky"></section>
<svg class="hero-arrow" style="left:66px" width="30" height="54" viewBox="0 0 30 54"><path d="M26 4 L4 27 L26 50" fill="none" stroke="#fff" stroke-width="5"/></svg>
<svg class="hero-arrow" style="left:1126px" width="30" height="54" viewBox="0 0 30 54"><path d="M4 4 L26 27 L4 50" fill="none" stroke="#fff" stroke-width="5"/></svg>
<h1 class="hero-title">Welcome to Valdora</h1>
<p class="hero-sub">Eport Flowers, Chocolate, &amp; Bananas</p>
<div class="btn" style="left:505px;top:426px;width:195px;height:53px;font-size:19px">Learn More</div>
<svg class="hero-wave" width="1200" height="130" viewBox="0 0 1200 130">
  <path d="M0 48 C300 110 600 0 1200 60 L1200 130 L0 130 Z" fill="#fff"/>
  <path d="M0 40 C200 80 420 80 640 30 C850 -10 1050 40 1200 100 L1200 108 C1050 55 850 10 640 48 C420 92 200 95 0 52 Z" fill="var(--green)"/>
  <path d="M0 56 C200 100 420 100 640 52 C850 15 1050 62 1200 112 L1200 118 C1050 72 850 28 640 62 C420 108 200 108 0 62 Z" fill="var(--green-dark)"/>
</svg>

<div class="mountain-band" role="img" aria-label="Soft snowy mountain range in grey tones"></div>
<h2 class="section-title about-title">About <em>Valdora</em></h2>
<p class="about-text">Fusce tellus Sed metus augue convallis et vehicula ut pulvinar eu ante Integer orci tellus tristique vitae consequat nec porta vel lectus Nulla sit amet diam aliquam enim Proin dui lectus cursus eu mattis laoreet viverra sit amet quam Curabitur vel dolor ultrices ipsum dictum tristique</p>

<article class="product" style="left:121px">
  <div class="product-photo" role="img" aria-label="Colourful bouquet of roses and tropical flowers" style="background:linear-gradient(135deg,#c44a8a,#f07a30 40%,#e9e0d0 60%,#6a9a3a)"></div>
  <div class="product-card"><h3>Flowers</h3><p>Curabitur vel dolor ultrices ipsum dictum tristique Praesent vitae lacus Ut velit enim vestibulum non fermentum nec</p><div class="btn">Learn More</div></div>
</article>
<article class="product" style="left:451px">
  <div class="product-photo" role="img" aria-label="Assorted chocolate truffles" style="background:linear-gradient(135deg,#8a5a3a,#3a2218 45%,#c9a07a 65%,#2a1810)"></div>
  <div class="product-card"><h3>Chocolate</h3><p>Curabitur vel dolor ultrices ipsum dictum tristique Praesent vitae lacus Ut velit enim vestibulum non fermentum nec</p><div class="btn">Learn More</div></div>
</article>
<article class="product" style="left:783px">
  <div class="product-photo" role="img" aria-label="Bunch of bananas growing on the plant" style="background:linear-gradient(135deg,#d9b43a,#c39a28 35%,#5f9a2a 65%,#86c040)"></div>
  <div class="product-card"><h3>Bananas</h3><p>Curabitur vel dolor ultrices ipsum dictum tristique Praesent vitae lacus Ut velit enim vestibulum non fermentum nec</p><div class="btn">Learn More</div></div>
</article>

<section class="why">
  <div class="why-photo" role="img" aria-label="Box of fresh green bananas packed for export"></div>
  <h2>Why Choose Us</h2>
  <div class="why-rule"></div>
  <div class="why-text">
    <p>Fusce tellus Sed metus augue convallis et vehicula ut pulvinar eu ante Integer orci tellus tristique vitae consequat nec porta</p>
    <p>vel lectus Nulla sit amet diam aliquam enim Proin dui lectus cursus eu mattis laoreet viverra sit amet quam Curabitur vel dolor ultrices ipsum dictum tristique Praesent vitae lacus Ut velit enim vestibulum non fermentum nec hendrerit quis leo Pellentesque rutrum</p>
  </div>
  <div class="btn">Learn More</div>
</section>

<section class="benefits"></section>
<svg class="why-edge" width="1200" height="104" viewBox="0 0 1200 104">
  <path d="M0 104 L0 98 L20 86 L40 92 L70 60 L110 54 L150 48 L200 50 L260 44 L320 48 L380 36 L440 42 L500 32 L560 38 L620 30 L660 36 L700 18 L740 10 L760 0 L790 14 L830 30 L870 24 L910 44 L960 38 L1010 52 L1060 46 L1110 60 L1160 66 L1200 58 L1200 104 Z" fill="var(--soft)"/>
</svg>
<h2 class="section-title benefits-title">Featured Benefits</h2>
<svg class="abs" style="left:0;top:2100px" width="1200" height="320" viewBox="0 0 1200 320">
  <g fill="none" stroke="#999" stroke-width="1.5" stroke-dasharray="2 4">
    <path d="M378 60 C420 70 400 150 492 160"/>
    <path d="M822 60 C780 70 800 150 706 160"/>
    <path d="M540 205 C480 235 440 215 430 260"/>
    <path d="M660 205 C720 235 760 215 776 260"/>
    <path d="M598 208 L598 255"/>
  </g>
</svg>
<div class="hub">Valdora</div>

<div class="benefit" style="left:250px;top:2108px">
  <div class="ring"><svg width="46" height="46" viewBox="0 0 46 46" fill="none" stroke="var(--orange)" stroke-width="2"><path d="M16 6 h14 l-3 6 h-8 Z"/><path d="M14 30 C10 22 16 12 23 12 C30 12 36 22 32 30 Z"/><path d="M5 36 h12 l8 4 h14"/><text x="19" y="27" font-size="11" fill="var(--orange)" stroke="none" font-family="sans-serif">$</text></svg></div>
  <h4>Save Cost</h4><p>Augiat in pede Fusce tellus Sed metus</p><div class="num">01</div>
</div>
<div class="benefit" style="left:793px;top:2108px">
  <div class="ring"><svg width="46" height="46" viewBox="0 0 46 46" fill="none" stroke="var(--orange)" stroke-width="2"><circle cx="23" cy="23" r="18"/><path d="M23 12 V23 H32"/></svg></div>
  <h4>24/7 Available</h4><p>Augiat in pede Fusce tellus Sed metus</p><div class="num">05</div>
</div>
<div class="benefit" style="left:344px;top:2318px">
  <div class="ring"><svg width="46" height="46" viewBox="0 0 46 46" fill="none" stroke="var(--orange)" stroke-width="2"><circle cx="23" cy="20" r="13"/><circle cx="23" cy="20" r="8"/><path d="M15 31 L11 42 L17 39 L20 44 L23 34 L26 44 L29 39 L35 42 L31 31"/></svg></div>
  <h4>Quality Product</h4><p>Augiat in pede Fusce tellus Sed metus</p><div class="num">02</div>
</div>
<div class="benefit" style="left:518px;top:2361px">
  <div class="ring"><svg width="46" height="46" viewBox="0 0 46 46" fill="none" stroke="var(--orange)" stroke-width="2"><path d="M6 14 h22 v16 H6 Z"/><path d="M28 19 h7 l5 6 v5 h-12"/><circle cx="13" cy="32" r="3"/><circle cx="33" cy="32" r="3"/></svg></div>
  <h4>Free Shipping</h4><p>Augiat in pede Fusce tellus Sed metus</p><div class="num">03</div>
</div>
<div class="benefit" style="left:700px;top:2318px">
  <div class="ring"><svg width="46" height="46" viewBox="0 0 46 46" fill="none" stroke="var(--orange)" stroke-width="2"><circle cx="23" cy="23" r="16"/><ellipse cx="23" cy="23" rx="7" ry="16"/><path d="M7 23 H39 M10 15 H36 M10 31 H36"/></svg></div>
  <h4>Export Globally</h4><p>Augiat in pede Fusce tellus Sed metus</p><div class="num">04</div>
</div>

<section class="blogs">
  <h2>Recent Blogs</h2>
  <article class="post" style="left:136px">
    <div class="post-photo" role="img" aria-label="Chocolatiers at work in a kitchen" style="background:linear-gradient(135deg,#e8e4de,#8a7a6a 50%,#3a2a20)"></div>
    <div class="post-card"><div class="date">13 JAN 2020</div><h3>Augiat in pede Fusce tellus<br>Sed metus augue</h3><p>Morbi eget arcu Morbi porta libero<br>id ullamcorper nonummy nibh</p><div class="more">READ MORE</div></div>
  </article>
  <article class="post" style="left:457px">
    <div class="post-photo" role="img" aria-label="Banana plantation under a blue sky" style="background:linear-gradient(180deg,#2f6fc0,#7fb0e0 35%,#4d8a2a 60%,#2e5a18)"></div>
    <div class="post-card"><div class="date">10 JAN 2020</div><h3>Augiat in pede Fusce tellus<br>Sed metus augue</h3><p>Morbi eget arcu Morbi porta libero<br>id ullamcorper nonummy nibh</p><div class="more">READ MORE</div></div>
  </article>
  <article class="post" style="left:777px">
    <div class="post-photo" role="img" aria-label="Crates of pink and red flowers at a market" style="background:linear-gradient(135deg,#c8442a,#e36ab0 40%,#d15aa8 65%,#3a3a3a)"></div>
    <div class="post-card"><div class="date">05 JAN 2020</div><h3>Augiat in pede Fusce tellus<br>Sed metus augue</h3><p>Morbi eget arcu Morbi porta libero<br>id ullamcorper nonummy nibh</p><div class="more">READ MORE</div></div>
  </article>
</section>

<footer class="site-footer">
  <div class="foot-col" style="left:160px">
    <h5>MENU</h5>
    <div class="menu-list">About Us<br>Our Services<br>Export<br>Testimonials<br>Blogs<br>Contact Us</div>
  </div>
  <div class="foot-col" style="left:332px">
    <h5>CONTACT US</h5>
    <div class="contact-row"><span class="icon-dot"><svg width="16" height="18" viewBox="0 0 16 18"><path d="M8 1 C4 1 2 4 2 7 C2 11 8 17 8 17 C8 17 14 11 14 7 C14 4 12 1 8 1 Z" fill="#fff"/><circle cx="8" cy="7" r="2.3" fill="var(--green)"/></svg></span><span>42 Alder Lane #5<br>Austin TX 78701</span></div>
    <div class="contact-row"><span class="icon-dot"><svg width="16" height="16" viewBox="0 0 16 16"><path d="M3 1 L6 1 L7 5 L5 6 C6 8 8 10 10 11 L11 9 L15 10 L15 13 C15 14 14 15 13 15 C6 15 1 10 1 3 C1 2 2 1 3 1 Z" fill="#fff"/></svg></span><span>Call Us<br>555.010.2040</span></div>
    <div class="contact-row"><span class="icon-dot"><svg width="16" height="12" viewBox="0 0 16 12"><rect x="0.5" y="0.5" width="15" height="11" fill="#fff"/><path d="M1 1 L8 7 L15 1" fill="none" stroke="var(--green)" stroke-width="1.5"/></svg></span><span>Email Us<br>info@valdoraexport.com</span></div>
  </div>
  <div class="foot-col" style="left:619px">
    <h5>GET UPDATES</h5>
    <div style="font-size:15px">Subscribe for Our Newsletters</div>
    <div class="signup">ENTER EMAIL ADDRESS</div>
    <div class="subscribe">SUBSCRIBE</div>
  </div>
  <div class="foot-col" style="left:907px">
    <h5>GET IN TOUCH</h5>
    <div class="social"><span class="social-ring"></span><div><small>Like us on</small><span>Facepage</span></div></div>
    <div class="social"><span class="social-ring"></span><div><small>Follow us on</small><span>Chirper</span></div></div>
    <div class="social"><span class="social-ring"></span><div><small>Follow us on</small><span>Linkwork</span></div></div>
  </div>
  <div class="foot-rule"></div>
  <div class="copyright">Copyright © 2020 All right reserved</div>
</footer>

</body>
</html>
```